Shopping centre customer engagement software website

We need a multi page site with :

*What we do.
*How it works.
*Benefits
* Case study
* Testimonial
* Business login (we provide link to business portal)
* Consumer login (we provide link to consumer site)
* Book a demo
* Contact us

We want it to be clean and crisp and very self explanatory with little clutter. We are thinking white but are open to what ever looks the best.
Updates

Wordpress is preferred

Need extra days to review

Target Market(s)

Shopping centre managers and retail property companies

Coding

Coded - Design and coding required

Number of Pages Required

5+ page

Font styles to use
Sans Serif

Colors
ffffff

Requirements
Must have
• As listed above and must be responsive! Checkout our existing site for the text to be included (will be edited but it’ll give you an idea) www.vostrelink.com

```html
<!DOCTYPE html>
<html lang="en">
<head>
<meta charset="utf-8">
<title>Vostrelink – Shopping Centre Engagement</title>
<link rel="stylesheet" href="https://fonts.googleapis.com/css2?family=Raleway:ital,wght@0,200;0,400;0,500;0,600;0,700;1,400&display=swap">
<style>
:root{
  --teal:#5bbccc;
  --teal-dark:#43a6b7;
  --ink:#2e2e2e;
  --text:#666;
  --muted:#999;
  --panel:#f1f1f1;
  --panel-2:#e8e8e8;
  --contact:#f5f5f5;
  --white:#fff;
}
*{box-sizing:border-box;margin:0;padding:0}
html,body{width:1200px;height:3614px;overflow:hidden}
body{font-family:"Raleway",sans-serif;color:var(--text);background:var(--white);position:relative}
section,header,footer{position:absolute;left:0;width:1200px}
.abs{position:absolute}
.btn{display:inline-flex;align-items:center;justify-content:center;border-radius:30px;font-size:13px;font-weight:600;text-transform:uppercase;letter-spacing:.5px;text-decoration:none}
.btn-teal{background:var(--teal);color:var(--white)}
.btn-outline{border:2px solid var(--teal);color:var(--teal);background:var(--white)}
.heading{font-weight:700;color:var(--ink);font-size:30px;letter-spacing:1px;text-transform:uppercase}
.body-copy{font-size:12px;line-height:19px;color:var(--text)}

/* header */
.site-header{top:0;height:110px;background:var(--white)}
.brand{left:100px;top:12px;width:90px;display:flex;flex-direction:column;align-items:center;gap:6px;font-size:13px;font-weight:500;color:var(--ink);letter-spacing:1px}
.brand-dot{width:48px;height:48px;border-radius:50%;background:#b8bcc2}
.main-nav a{position:absolute;top:46px;font-size:13px;font-weight:600;color:var(--ink);text-decoration:none;letter-spacing:.5px}
.nav-demo{left:800px;top:33px;width:140px;height:40px}
.nav-login{left:954px;top:33px;width:147px;height:40px}

/* hero */
.hero{top:110px;height:613px;overflow:hidden}
.hero-photo{inset:0;background:linear-gradient(180deg,#8f9aa3 0%,#b4bcc2 40%,#707a82 80%,#5f6870 100%)}
.hero-shade{inset:0;background:linear-gradient(90deg,rgba(40,50,60,.35),rgba(40,50,60,.05))}
.hero-title{left:96px;top:215px;font-size:100px;font-weight:200;color:var(--white);letter-spacing:10px;line-height:1}
.hero-sub{left:98px;top:345px;width:600px;font-size:22px;font-weight:500;color:var(--white);line-height:1.65}
.hero-demo{left:730px;top:376px;width:170px;height:42px}
.hero-video{left:918px;top:376px;width:180px;height:42px;border:2px solid var(--white);color:var(--white);gap:10px}
.hero-video svg{width:24px;height:24px}
.hero-curve{left:0;bottom:0;width:1200px;height:200px}

/* welcome */
.welcome{top:723px;height:518px}
.dash-visual{left:96px;top:100px;width:430px;height:300px;border-radius:6px;background:linear-gradient(160deg,#2b3138 0%,#3b434c 20%,#eef2f5 21%,#f5f0e6 100%)}
.welcome-title{left:602px;top:140px}
.welcome-copy{left:602px;top:195px;width:500px}
.welcome-more{left:602px;top:364px;width:150px;height:44px}

/* what we do */
.what{top:1241px;height:494px}
.what-panel{left:0;top:0;width:602px;height:494px;background:var(--panel)}
.what-title{left:100px;top:70px}
.what-copy{left:100px;top:130px;width:500px}
.what-copy p+p{margin-top:19px}
.what-more{left:100px;top:380px;width:150px;height:44px}
.what-photo{left:602px;top:0;width:598px;height:494px;background:linear-gradient(135deg,#3a4a5a 0%,#6b7580 45%,#c9a97a 75%,#5a6470 100%)}

/* benefits */
.benefits{top:1735px;height:482px}
.benefits-photo{left:0;top:0;width:602px;height:482px;background:linear-gradient(135deg,#dfe3e6 0%,#f2f2f0 40%,#9db5d0 70%,#cfd3d6 100%)}
.benefits-panel{left:602px;top:0;width:598px;height:482px;background:var(--panel-2)}
.benefits-title{left:60px;top:64px}
.benefits-intro{left:60px;top:118px;width:460px;font-size:12px;line-height:1.8;color:#a9b0b3}
.benefit-list{left:70px;top:205px;width:460px;display:flex;justify-content:space-between}
.benefit{width:140px;text-align:center}
.benefit-icon{width:100px;height:100px;margin:0 auto}
.benefit p{margin-top:10px;font-size:12px;line-height:1.6;color:var(--ink)}
.chev{top:240px;width:20px;height:30px}
.benefits-more{left:222px;top:386px;width:88px;height:30px;font-size:10px;text-transform:none}

/* how it works */
.how{top:2217px;height:525px;text-align:center}
.how-title{left:0;width:1200px;top:100px}
.how-sub{left:0;width:1200px;top:150px;font-size:13px;line-height:1.7;color:var(--text)}
.steps{left:0;top:255px;width:1200px;height:240px}
.step{position:absolute;width:200px;text-align:center}
.step-circle{width:136px;height:136px;margin:0 auto;border-radius:50%;background:var(--white);box-shadow:0 2px 10px rgba(0,0,0,.12);position:relative;display:flex;align-items:center;justify-content:center}
.step-num{position:absolute;right:-4px;bottom:4px;width:28px;height:28px;border-radius:50%;background:var(--teal);color:var(--white);font-size:12px;font-weight:700;display:flex;align-items:center;justify-content:center;border:2px solid var(--white)}
.step-label{margin-top:16px;font-size:16px;font-weight:600;color:var(--ink)}
.step-arrow{position:absolute;top:40px;width:100px;height:40px}

/* case study */
.case{top:2742px;height:555px;overflow:hidden}
.case-bg{inset:0;background:linear-gradient(120deg,#2d3038 0%,#4b4f58 40%,#7b6a66 70%,#3a3d46 100%)}
.case-shade{inset:0;background:rgba(20,22,28,.35)}
.case-title{left:0;width:1200px;top:70px;text-align:center;color:var(--white);font-size:28px;font-weight:600;letter-spacing:1px}
.case-card{left:101px;top:167px;width:407px;height:320px;background:var(--white)}
.case-card-photo{left:0;top:0;width:407px;height:258px;background:linear-gradient(150deg,#8fa8c2,#c7cfd7 60%,#9aa9b8)}
.case-card-foot{left:26px;top:275px;display:flex;align-items:center;gap:14px;font-size:14px;font-weight:700;color:var(--ink)}
.case-card-foot span.count{display:flex;align-items:center;gap:8px;font-weight:500;color:var(--text)}
.quote{left:602px;top:160px;width:540px;font-size:13px;font-style:italic;line-height:1.9;color:var(--white)}
.quote-author{left:945px;top:372px;color:var(--white);font-size:13px;line-height:2}
.quote-author strong{font-size:14px}
.case-arrow{top:300px;width:24px;height:40px}

/* contact */
.contact{top:3297px;height:241px;background:var(--contact)}
.contact-title{left:100px;top:66px;font-size:18px;font-weight:700;color:var(--ink);letter-spacing:.5px}
.contact-col{top:118px;font-size:11px;line-height:1.9;color:var(--text)}
.contact-line{display:flex;gap:12px;margin-bottom:8px}
.contact-line svg{width:12px;height:12px;margin-top:4px;flex:none}
.social{top:118px;display:flex;gap:13px}
.social span{width:40px;height:40px;border-radius:50%;border:1px solid #cfcfcf;background:var(--white);display:flex;align-items:center;justify-content:center}
.social span i{width:10px;height:10px;border-radius:50%;background:#555;display:block}

/* footer */
.site-footer{top:3538px;height:76px;border-top:1px solid #e2e2e2;display:flex;align-items:center;justify-content:center;font-size:11px;color:var(--text)}
</style>
</head>
<body>

<header class="site-header">
  <div class="brand abs"><span class="brand-dot"></span>VOSTRELINK</div>
  <nav class="main-nav">
    <a style="left:282px">WHAT WE DO</a>
    <a style="left:417px">BENEFITS</a>
    <a style="left:528px">HOW IT WORKS</a>
    <a style="left:675px">CASE STUDY</a>
  </nav>
  <a class="btn btn-teal abs nav-demo">Request Demo</a>
  <a class="btn btn-outline abs nav-login">Business Login</a>
</header>

<section class="hero">
  <div class="hero-photo abs" role="img" aria-label="Interior of a multi-level shopping centre with escalators and shoppers"></div>
  <div class="hero-shade abs"></div>
  <div class="hero-title abs">VOSTRELINK</div>
  <p class="hero-sub abs">Vostrelink exceeds all expectations for Shopping Centre Managers, Shoppers, Tenants and Landlords</p>
  <a class="btn btn-teal abs hero-demo">Request a Demo</a>
  <a class="btn abs hero-video">Watch Video
    <svg viewBox="0 0 24 24"><circle cx="12" cy="12" r="11" fill="#fff"/><path d="M10 8l6 4-6 4z" fill="#555"/></svg>
  </a>
  <svg class="hero-curve abs" viewBox="0 0 1200 200" preserveAspectRatio="none">
    <path d="M0 200 L0 170 C300 205 650 120 1200 60 L1200 200 Z" fill="#fff"/>
  </svg>
</section>

<section class="welcome">
  <div class="dash-visual abs" role="img" aria-label="Desktop monitor showing the analytics dashboard with coloured stat tiles and an area chart"></div>
  <h2 class="heading abs welcome-title">Welcome to Vostrelink</h2>
  <p class="body-copy abs welcome-copy">Lorem ipsum dolor sit amet, consectetur adipiscing elit, sed do eiusmod tempor incididunt ut labore et dolore magna aliqua. Ut enim ad minim veniam, nostrud exercitation ullamco laboris nisi ut aliquip ex ea commodo consequat. Duis aute dolor in reprehenderit in voluptate velit esse cillum dolore fugiat nullapariatur perspiciatis unde omnis iste natus error sit voluptatem accusantium doloremque laudantium, totam rem aperiam,</p>
  <a class="btn btn-teal abs welcome-more">Read More &gt;&gt;</a>
</section>

<section class="what">
  <div class="what-panel abs"></div>
  <h2 class="heading abs what-title">What We Do</h2>
  <div class="body-copy abs what-copy">
    <p>Vostrelink provides shopping centre managers with an easy to use platform which enables them to delight their shoppers, impress their tenants, provide detailed data to their landlords and all accessible to them at the click of button.</p>
    <p>Vostrelink gives shopping centres real time tracking through smart ID's of individual customer journeys through their physical stores, enabling highly targeted, relevant and timely promotional and rewarding capabilities. Furthermore, through deep analytical data processing of the customer journey, centre managers will be able to more accurately and reliably predict shopping behaviours.</p>
  </div>
  <a class="btn btn-teal abs what-more">Read More &gt;&gt;</a>
  <div class="what-photo abs" role="img" aria-label="Team working at computer screens in a bright office"></div>
</section>

<section class="benefits">
  <div class="benefits-photo abs" role="img" aria-label="Man working on a laptop at a desk in a light office"></div>
  <div class="benefits-panel abs">
    <h2 class="heading abs benefits-title">Benefits</h2>
    <p class="abs benefits-intro">At vero eos et accusamus et iusto odio dignissimos ducimus qui blanditiis praesentium voluptatum deleniti atque corrupti quos dolores quas molestias</p>
    <svg class="chev abs" style="left:12px" viewBox="0 0 20 30"><path d="M15 4L5 15l10 11" stroke="#888" stroke-width="3" fill="none"/></svg>
    <div class="benefit-list abs">
      <div class="benefit">
        <svg class="benefit-icon" viewBox="0 0 100 100"><circle cx="50" cy="50" r="46" fill="#fff" stroke="#5bbccc" stroke-width="6"/><rect x="34" y="30" width="32" height="12" rx="2" fill="#4a5a6a"/><rect x="34" y="46" width="32" height="12" rx="2" fill="#4a5a6a"/><circle cx="62" cy="64" r="9" fill="#e0624f"/></svg>
        <p>Easy to install,<br>no wiring required</p>
      </div>
      <div class="benefit">
        <svg class="benefit-icon" viewBox="0 0 100 100"><circle cx="50" cy="50" r="46" fill="#fff" stroke="#5bbccc" stroke-width="6"/><circle cx="50" cy="50" r="24" fill="#e0624f"/><rect x="40" y="38" width="20" height="24" rx="2" fill="#fff"/></svg>
        <p>Easy to use dashboard<br>with one click reporting</p>
      </div>
      <div class="benefit">
        <svg class="benefit-icon" viewBox="0 0 100 100"><circle cx="50" cy="50" r="46" fill="#fff" stroke="#5bbccc" stroke-width="6"/><path d="M32 58a10 10 0 0 1 4-19 14 14 0 0 1 27-2 10 10 0 0 1 4 21z" fill="#8fb8c8"/><rect x="44" y="58" width="12" height="10" fill="#4a5a6a"/></svg>
        <p>Have the data to back up<br>any decision's you make</p>
      </div>
    </div>
    <svg class="chev abs" style="left:506px" viewBox="0 0 20 30"><path d="M5 4l10 11L5 26" stroke="#888" stroke-width="3" fill="none"/></svg>
    <a class="btn btn-teal abs benefits-more">Read More</a>
  </div>
</section>

<section class="how">
  <h2 class="heading abs how-title">How It Works</h2>
  <p class="abs how-sub">Sed quia non numquam eius modi tempora incidunt ut labore et dolore<br>magnam aliquam quaerat voluptatem</p>
  <div class="steps abs">
    <div class="step" style="left:64px">
      <div class="step-circle"><svg width="56" height="44" viewBox="0 0 56 44"><rect x="2" y="6" width="40" height="26" rx="3" fill="#3d7fb8"/><rect x="12" y="14" width="40" height="26" rx="3" fill="#f2b640"/><rect x="12" y="20" width="40" height="5" fill="#c8902c"/></svg><span class="step-num">1</span></div>
      <div class="step-label">Allocate Cards</div>
    </div>
    <svg class="step-arrow" style="left:266px" viewBox="0 0 100 40"><path d="M4 34 Q50 4 86 20" stroke="#5bbccc" stroke-width="6" fill="none"/><path d="M80 8 L98 24 L76 30 Z" fill="#5bbccc"/></svg>
    <div class="step" style="left:286px">
      <div class="step-circle"><svg width="56" height="48" viewBox="0 0 56 48"><path d="M6 18h10l22-12v36L16 30H6z" fill="#2e4a6b"/><rect x="14" y="30" width="8" height="12" fill="#2e4a6b"/><circle cx="46" cy="12" r="5" fill="#e0624f"/><circle cx="50" cy="26" r="4" fill="#5bbccc"/><circle cx="46" cy="38" r="4" fill="#f2b640"/></svg><span class="step-num">2</span></div>
      <div class="step-label">Direct Marketing</div>
    </div>
    <svg class="step-arrow" style="left:480px" viewBox="0 0 100 40"><path d="M4 34 Q50 4 86 20" stroke="#5bbccc" stroke-width="6" fill="none"/><path d="M80 8 L98 24 L76 30 Z" fill="#5bbccc"/></svg>
    <div class="step" style="left:498px">
      <div class="step-circle"><svg width="48" height="56" viewBox="0 0 48 56"><path d="M14 30l-6 24 10-6 6 8 0-24z M34 30l6 24-10-6-6 8 0-24z" fill="#e0624f"/><circle cx="24" cy="22" r="18" fill="#2e4a6b"/><circle cx="24" cy="22" r="9" fill="#f2b640"/></svg><span class="step-num">3</span></div>
      <div class="step-label">Rewarding Loyalty</div>
    </div>
    <svg class="step-arrow" style="left:698px" viewBox="0 0 100 40"><path d="M4 34 Q50 4 86 20" stroke="#5bbccc" stroke-width="6" fill="none"/><path d="M80 8 L98 24 L76 30 Z" fill="#5bbccc"/></svg>
    <div class="step" style="left:720px">
      <div class="step-circle"><svg width="56" height="46" viewBox="0 0 56 46"><path d="M2 6h18l4 5h30v33H2z" fill="#f2b640"/><rect x="10" y="14" width="36" height="20" fill="#5bbccc"/><path d="M2 18h52l-4 26H2z" fill="#e8a630"/></svg><span class="step-num">4</span></div>
      <div class="step-label">Collect Data</div>
    </div>
    <svg class="step-arrow" style="left:914px" viewBox="0 0 100 40"><path d="M4 34 Q50 4 86 20" stroke="#5bbccc" stroke-width="6" fill="none"/><path d="M80 8 L98 24 L76 30 Z" fill="#5bbccc"/></svg>
    <div class="step" style="left:936px">
      <div class="step-circle"><svg width="52" height="52" viewBox="0 0 52 52"><circle cx="22" cy="22" r="16" fill="#fff" stroke="#2e4a6b" stroke-width="5"/><rect x="14" y="22" width="4" height="8" fill="#e0624f"/><rect x="20" y="16" width="4" height="14" fill="#5bbccc"/><rect x="26" y="19" width="4" height="11" fill="#f2b640"/><path d="M33 33l14 14" stroke="#2e4a6b" stroke-width="7" stroke-linecap="round"/></svg><span class="step-num">5</span></div>
      <div class="step-label">Data Analysis</div>
    </div>
  </div>
</section>

<section class="case">
  <div class="case-bg abs" role="img" aria-label="Blurred busy shopping street with passing shoppers"></div>
  <div class="case-shade abs"></div>
  <h2 class="case-title abs">CASE STUDY &amp; TESTIMONIAL</h2>
  <svg class="case-arrow abs" style="left:44px" viewBox="0 0 24 40"><path d="M20 4L4 20l16 16" stroke="#fff" stroke-width="4" fill="none"/></svg>
  <div class="case-card abs">
    <div class="case-card-photo abs" role="img" aria-label="Hand holding a smartphone showing a new message notification"></div>
    <svg class="abs" style="left:0;top:200px" width="407" height="60" viewBox="0 0 407 60" preserveAspectRatio="none"><path d="M0 60 L0 40 C120 10 260 70 407 30 L407 60Z" fill="#fff"/></svg>
    <div class="case-card-foot abs">MESSAGES SENT
      <span class="count"><svg width="18" height="16" viewBox="0 0 18 16"><path d="M2 2h14v9H8l-4 4v-4H2z" fill="#3d7fb8"/></svg>10500</span>
    </div>
  </div>
  <p class="quote abs">“ Sed ut perspiciatis unde omnis iste natus error sit voluptatem accusantium doloremque laudantium, totam rem aperiam, eaque ipsa quae ab illo inventore veritatis et quasi architecto beatae vitae dicta sunt explicabo. Nemo enim ipsam voluptatem quia voluptas sit aspernatur aut odit aut fugit, sed quia consequuntur magni dolores eos qui ratione voluptatem sequi nesciunt. Neque porro quisquam est, qui dolorem ipsum quia dolor sit amet, consectetur, adipisci velit, sed quia non numquam eius modi tempora incidunt ut labore et dolore magnam aliquam quaerat voluptatem. ”</p>
  <div class="quote-author abs"><strong>- Author Name</strong><br>City Location</div>
  <svg class="case-arrow abs" style="left:1132px" viewBox="0 0 24 40"><path d="M4 4l16 16L4 36" stroke="#fff" stroke-width="4" fill="none"/></svg>
</section>

<section class="contact">
  <h2 class="contact-title abs">CONTACT US</h2>
  <div class="contact-col abs" style="left:100px">
    <div class="contact-line"><svg viewBox="0 0 12 12"><path d="M11 1L1 5l5 1 1 5z" fill="#666"/></svg><span>Unit 7, Harbour Road<br>Carrowmore, CM12 4RT</span></div>
    <div class="contact-line"><svg viewBox="0 0 12 12"><rect x="1" y="2" width="10" height="8" fill="#666"/><path d="M1 2l5 4 5-4" stroke="#fff" fill="none"/></svg><span>dara@vostrelink.com</span></div>
  </div>
  <div class="contact-col abs" style="left:300px">
    <div class="contact-line"><svg viewBox="0 0 12 12"><path d="M11 1L1 5l5 1 1 5z" fill="#666"/></svg><span>Foundry, 3rd Floor 18 Kestrel<br>Lane, Westbury, WB4 2LN</span></div>
    <div class="contact-line"><svg viewBox="0 0 12 12"><rect x="1" y="2" width="10" height="8" fill="#666"/><path d="M1 2l5 4 5-4" stroke="#fff" fill="none"/></svg><span>tomas@vostrelink.com</span></div>
  </div>
  <div class="contact-col abs" style="left:520px">
    <div class="contact-line"><svg viewBox="0 0 12 12"><path d="M11 1L1 5l5 1 1 5z" fill="#666"/></svg><span>2nd Floor, Alder House<br>Alder Street, Carrowmore</span></div>
    <div class="contact-line"><svg viewBox="0 0 12 12"><rect x="1" y="2" width="10" height="8" fill="#666"/><path d="M1 2l5 4 5-4" stroke="#fff" fill="none"/></svg><span>niall@vostrelink.com</span></div>
  </div>
  <div class="contact-col abs" style="left:740px">
    <div class="contact-line"><svg viewBox="0 0 12 12"><path d="M2 1h3l1 3-2 1a7 7 0 0 0 3 3l1-2 3 1v3c-6 0-9-3-9-9z" fill="#666"/></svg><span>Phone | 0201 555 0184</span></div>
    <div class="contact-line"><svg viewBox="0 0 12 12"><rect x="1" y="2" width="10" height="8" fill="#666"/><path d="M1 2l5 4 5-4" stroke="#fff" fill="none"/></svg><span>Email | contact@vostrelink.com</span></div>
  </div>
  <div class="social abs" style="left:962px">
    <span><i></i></span><span><i></i></span><span><i></i></span>
  </div>
</section>

<footer class="site-footer">Copyrights © Vostrelink 2018. All Rights Reserved.</footer>

</body>
</html>
```